Website for a health information tech company

I need a website for a new startup company, Velorim Health, Inc. that specializes in healthcare information technology. Velorim Health is a monitoring system that uses wearable sensors and predictive algorithms to detect when an elderly persons health is declining and triggers progressively higher levels of interventions.

The site needs to be very simple, elegant and initially will have minimal information as company and product is still under development and is in a stealth mode. I like the lumotreva.com website as it has a "single page" look and feel with sliding vertical sections. Ideally the sections would be "Home", "Technology", "Customers", "News", "About Us" and "Contact Us". The contact us should have a contact form that gets sent to an email address.

I have a couple of example sites that my site should take inspiration from (lumotreva.com and bixendale.com). I would like a WordPress backend so I can easily update content so the winning design should be easily importable or setup into Wordpress.

Target Market(s)

Investors, Customers (Doctors, Patients, Health Insurance companies, Hospital directors)

Industry/Entity Type

Healthcare

Requirements
Must have
• top horizontal menu that gets repeated on each vertical slide. Should have animated vertical slides. Must be viewable on any device (iPad, Android Tablets) correctly and must render correctly on different screen sizes. Must be viewable in all popular browsers. Must work well with touchscreen devices such as iPad, iPhone, Android tablets and phones.
Must have a content management system backend such as WordPress so I can edit/update content and in future add additional sections, images etc.

See attached company logo so colors must be complimentary to the logo colors. Feel free to use the logo colors as web site theme colors if it makes sense.
Nice to have
• Nice subtle textured background like linen or leather.
Should not have
• Not looking for traditional web site design with nav bars on left etc
Should not feel like a traditional web site where you click a link and another page loads. It must be animated slide into a different section. No flash or any other technology that requires plug ins.

```html
<!DOCTYPE html>
<html lang="en">
<head>
<meta charset="utf-8">
<title>Velorim Health</title>
<link rel="stylesheet" href="https://fonts.googleapis.com/css2?family=Source+Sans+3:wght@300;400;600;700&family=Roboto+Condensed:wght@700&display=swap">
<style>
:root{
  --orange:#f7801c;
  --orange-dark:#e86c0a;
  --ink:#333;
  --text:#5a5a5a;
  --muted:#8a8a8a;
  --header-bg:#f3f3f3;
  --line:#d6d6d6;
  --footer-bg:#4b4b4b;
  --footer-text:#c9c9c9;
  --topbar:#6b6b6b;
}
*{box-sizing:border-box;margin:0;padding:0}
html,body{width:1011px;height:1200px;overflow:hidden;background:#fff}
body{position:relative;font-family:"Source Sans 3",sans-serif;color:var(--text)}
.topbar{position:absolute;left:0;top:0;width:1011px;height:5px;background:var(--topbar)}
.site-header{position:absolute;left:0;top:5px;width:1011px;height:123px;background:var(--header-bg)}
.brand{position:absolute;left:66px;top:58px;display:flex;align-items:center;gap:10px;font-size:27px;font-weight:600;color:var(--orange);letter-spacing:.3px}
.brand-mark{width:24px;height:24px;border-radius:50%;background:var(--orange)}
.social{position:absolute;left:856px;top:24px;display:flex;gap:7px}
.social span{width:17px;height:17px;border-radius:50%;background:#7a7a7a}
.main-nav{position:absolute;right:82px;top:64px;display:flex;font-size:17px;color:#444}
.main-nav a{color:inherit;text-decoration:none;padding:0 13px;border-left:1px solid var(--line);line-height:20px}
.main-nav a:first-child{border-left:0}
.main-nav a:last-child{padding-right:0}
.hero{position:absolute;left:0;top:128px;width:1011px;height:402px;background:linear-gradient(#fafafa,#f0f0f0)}
.hero-title{position:absolute;left:84px;top:64px;color:var(--orange);line-height:1}
.hero-title .light{display:block;font-size:32px;font-weight:300}
.hero-title .bold{display:block;font-size:36px;font-weight:700;margin-top:6px}
.hero-sub{position:absolute;left:86px;top:141px;font-size:17px;color:#444}
.hero-text{position:absolute;left:85px;top:168px;width:350px;font-size:12.2px;line-height:17px;font-weight:300;color:#666}
.btn-learn{position:absolute;left:84px;top:229px;width:90px;height:27px;background:#2f2f2f;border-radius:3px;color:#fff;font-family:"Roboto Condensed",sans-serif;font-size:12.5px;display:flex;align-items:center;justify-content:center}
.slider-dots{position:absolute;left:84px;top:289px;display:flex;gap:4px}
.slider-dots span{width:10px;height:10px;border-radius:50%;background:#cfcfcf}
.slider-dots span.active{background:#111}
.arrow{position:absolute;top:150px}
.arrow.prev{left:27px}
.arrow.next{left:953px}
.device-visual{position:absolute;left:470px;top:34px;width:445px;height:334px;border-radius:16px;background:linear-gradient(135deg,#3a3a3a,#111 60%,#2a2a2a)}
.features{position:absolute;left:0;top:560px;width:1011px}
.feature{position:absolute;top:0;width:270px}
.feature h3{display:flex;align-items:center;gap:8px;font-size:18.5px;font-weight:400;color:var(--orange);height:32px}
.feature p{margin-top:3px;font-size:12.2px;line-height:17px;font-weight:300;color:#777}
.section-rule{position:absolute;left:20px;width:971px;height:30px;background:radial-gradient(ellipse at top,rgba(0,0,0,.05),rgba(0,0,0,0) 70%)}
.welcome{position:absolute;left:69px;top:742px;width:550px}
.welcome h2,.contact h2{font-size:24px;font-weight:400;color:var(--ink)}
.welcome p{margin-top:11px;font-size:13.6px;line-height:20.8px;font-weight:300;color:#444}
.welcome p + p{margin-top:9px}
.divider-v{position:absolute;left:641px;top:744px;width:1px;height:188px;background:#ddd}
.contact{position:absolute;left:669px;top:742px;width:266px}
.contact .field{margin-top:8px;height:34px;border:1px solid var(--line);background:#fff;padding-left:14px;font-size:13.5px;color:#999;display:flex;align-items:center;font-weight:300}
.contact h2 + .field{margin-top:10px}
.btn-submit{margin-top:10px;margin-left:3px;width:95px;height:34px;border-radius:3px;background:linear-gradient(var(--orange),var(--orange-dark));color:#fff;font-size:15.5px;font-weight:600;display:flex;align-items:center;justify-content:center}
.partners{position:absolute;left:0;top:1010px;width:1011px;height:60px}
.partner{position:absolute;background:#b4b4b4}
.site-footer{position:absolute;left:0;top:1110px;width:1011px;height:90px;background:var(--footer-bg);color:var(--footer-text)}
.copyright{position:absolute;left:66px;top:30px;font-size:12.2px;font-weight:300}
.footer-nav{position:absolute;right:80px;top:28px;display:flex;font-size:13px;color:#e6e6e6}
.footer-nav a{color:inherit;text-decoration:none;padding:0 6px;border-left:1px solid #ccc;line-height:14px}
.footer-nav a:first-child{border-left:0}
.footer-nav a:last-child{padding-right:0}
</style>
</head>
<body>
<div class="topbar"></div>

<header class="site-header">
  <div class="brand"><span class="brand-mark"></span>Velorim Health</div>
  <div class="social" aria-label="Social links"><span></span><span></span><span></span></div>
  <nav class="main-nav">
    <a href="#">Home</a><a href="#">Technology</a><a href="#">Customers</a><a href="#">About Us</a><a href="#">Contact Us</a>
  </nav>
</header>

<section class="hero">
  <h1 class="hero-title"><span class="light">PATIENT PENDING</span><span class="bold">MONITORING SYSTEM</span></h1>
  <p class="hero-sub">Mauris vel lacus vitae vestibulum volutpat.</p>
  <p class="hero-text">Mauris vel lacus vitae felis vestibulum volutpat. Etiam est nunc, venenatis in, tristique eu, imperdiet ac, nisl. Cum sociis natoque penatibus et magnis dis parturient montes</p>
  <div class="btn-learn">LEARN MORE</div>
  <div class="slider-dots"><span class="active"></span><span></span><span></span><span></span></div>
  <svg class="arrow prev" width="30" height="74" viewBox="0 0 30 74"><polyline points="28,1 2,37 28,73" fill="none" stroke="#888" stroke-width="1.5"/></svg>
  <svg class="arrow next" width="30" height="74" viewBox="0 0 30 74"><polyline points="2,1 28,37 2,73" fill="none" stroke="#888" stroke-width="1.5"/></svg>
  <div class="device-visual" role="img" aria-label="Tablet and smartphone showing a monitoring dashboard with follower statistics and a line chart"></div>
</section>

<section class="features">
  <div class="feature" style="left:65px">
    <h3><svg width="42" height="28" viewBox="0 0 42 28"><path d="M2 14 Q21 -6 40 14 Q21 34 2 14Z" fill="none" stroke="#f7801c" stroke-width="4"/><circle cx="21" cy="14" r="7" fill="#f7801c"/></svg>Monitoring Featured</h3>
    <p>Nunc tempus felis vitae urna. Vivamus porttitor, g, purus nisi eleifend libero, a tempus</p>
  </div>
  <div class="feature" style="left:369px">
    <h3><svg width="36" height="28" viewBox="0 0 36 28" fill="none" stroke="#f7801c" stroke-width="4"><path d="M1 6 H9 C18 6 16 22 25 22 H31"/><path d="M1 22 H9 C18 22 16 6 25 6 H31"/><path d="M28 1 L34 6 L28 11" /><path d="M28 17 L34 22 L28 27"/></svg>Our Technology</h3>
    <p>Nunc tempus felis vitae urna. Vivamus porttitor, g, purus nisi eleifend libero, a tempus</p>
  </div>
  <div class="feature" style="left:673px">
    <h3><svg width="44" height="34" viewBox="0 0 44 34" fill="none" stroke="#f7801c" stroke-width="3.5"><ellipse cx="17" cy="13" rx="15" ry="10"/><path d="M8 21 L5 30 L15 23"/><path d="M31 10 C40 12 43 20 37 25 L39 32 L31 27 C26 28 22 27 20 25"/></svg>Customer Service</h3>
    <p>Nunc tempus felis vitae urna. Vivamus porttitor, g, purus nisi eleifend libero, a tempus</p>
  </div>
</section>

<div class="section-rule" style="top:674px"></div>

<section class="welcome">
  <h2>Welcome to Our Website Mainpage..</h2>
  <p>Velorim Health is a patent pending monitoring system that uses wearable sensors and predictive algorithms to detect when an elderly persons health is declining and triggers progressively higher levels of interventions.</p>
  <p>The goal is to allow an elderly person, who often has 2 or more chronic conditions, to age in place and stay independent as long as possible by the use of&nbsp; intelligent monitoring to deliver just in time care.</p>
</section>

<div class="divider-v"></div>

<section class="contact">
  <h2>Let’s get in Touch</h2>
  <div class="field">Name</div>
  <div class="field">Email address</div>
  <div class="field">Company/organization</div>
  <div class="btn-submit">Submit</div>
</section>

<div class="section-rule" style="top:978px"></div>

<section class="partners" aria-label="Partners">
  <div class="partner" style="left:107px;top:12px;width:36px;height:36px"></div>
  <div class="partner" style="left:174px;top:18px;width:18px;height:18px;border-radius:50%"></div>
  <div class="partner" style="left:303px;top:12px;width:80px;height:26px"></div>
  <div class="partner" style="left:410px;top:16px;width:26px;height:26px;border-radius:50%"></div>
  <div class="partner" style="left:514px;top:23px;width:87px;height:20px;background:#222"></div>
  <div class="partner" style="left:634px;top:24px;width:30px;height:16px"></div>
  <div class="partner" style="left:718px;top:0px;width:36px;height:36px;border-radius:50%"></div>
  <div class="partner" style="left:808px;top:14px;width:32px;height:32px;border-radius:50%"></div>
</section>

<footer class="site-footer">
  <p class="copyright">© 2013 Company Name.&nbsp; All right reserved.&nbsp; Term of Use</p>
  <nav class="footer-nav">
    <a href="#">Home</a><a href="#">Technology</a><a href="#">Customers</a><a href="#">About Us</a><a href="#">Contact Us</a>
  </nav>
</footer>
</body>
</html>
```